Small Business Broker Business Card Design

A business card design for a small business brokerage, which is a financial service, not unlike real estate brokerage, but for small businesses such as laundromats, pizza shops, restaurants, cleaners etc. The designs should all be simple, more conservative in nature, using the colors and font of the logo. Again, think real estate Brokerage as a business context
Contact Information for Business Card
Name: Glen R. Harlow. Title: Small Business Advisor. Email: g.harlow@bayfieldcapitalworks.example. Mobile: (555) 274-3918. Office: (555) 806-2147. www.bayfieldcapitalworks.example

```html
<!DOCTYPE html>
<html lang="en">
<head>
<meta charset="utf-8">
<title>Bayfield Capital Works – Business Card</title>
<link href="https://fonts.googleapis.com/css2?family=Montserrat:wght@600;700&family=Arimo:wght@400&display=swap" rel="stylesheet">
<style>
  :root {
    --navy: #17305f;
    --green: #7cbb35;
    --white: #ffffff;
    --ink: #4a4a4a;
    --stage: #e9ebee;
  }
  * { margin: 0; padding: 0; box-sizing: border-box; }
  html, body { width: 1200px; height: 963px; overflow: hidden; }
  body {
    background: var(--stage);
    display: flex; flex-direction: column; align-items: center; justify-content: center;
    gap: 48px;
  }
  .card {
    position: relative;
    width: 720px; height: 412px;
    border-radius: 22px;
    overflow: hidden;
    box-shadow: 0 6px 20px rgba(0,0,0,.12);
  }
  .card-front { background: var(--white); }
  .card-back { background: var(--green); }
  .front-bands { position: absolute; inset: 0; }

  .brand { position: absolute; }
  .brand-row { display: flex; align-items: center; gap: 10px; }
  .brand-square { width: 16px; height: 16px; background: var(--navy); flex: none; }
  .brand-name {
    font-family: "Montserrat", sans-serif; font-weight: 700;
    font-size: 22px; letter-spacing: 1.2px; text-transform: uppercase;
    color: var(--navy); white-space: nowrap;
  }
  .brand-tagline {
    font-family: "Montserrat", sans-serif; font-weight: 600;
    font-size: 10.5px; letter-spacing: 1.4px; text-transform: uppercase;
    color: var(--green); margin-top: 4px; padding-left: 26px; white-space: nowrap;
  }
  .card-front .brand { left: 100px; top: 176px; }

  .contacts {
    position: absolute; left: 44px; top: 262px;
    list-style: none;
    font-family: "Arimo", sans-serif; font-size: 15px; color: var(--ink);
  }
  .contacts li { display: flex; align-items: center; gap: 10px; height: 27px; white-space: nowrap; }
  .contacts svg { width: 14px; height: 14px; flex: none; }

  .person { position: absolute; right: 56px; top: 292px; }
  .person-name {
    font-family: "Montserrat", sans-serif; font-weight: 700;
    font-size: 28px; letter-spacing: 1px; text-transform: uppercase; color: var(--navy);
    white-space: nowrap;
  }
  .person-title {
    font-family: "Arimo", sans-serif; font-size: 19px; color: var(--green); margin-top: 2px;
  }
  .accent-tab {
    position: absolute; right: 0; top: 322px; width: 40px; height: 34px; background: var(--green);
  }

  .card-back .brand { left: 60px; top: 172px; }
  .card-back .brand-square { background: var(--white); }
  .card-back .brand-name { color: var(--white); font-size: 27px; }
  .card-back .brand-tagline { color: var(--white); font-size: 12.5px; }
</style>
</head>
<body>

<section class="card card-front" aria-label="Card front">
  <svg class="front-bands" viewBox="0 0 720 412" aria-hidden="true">
    <path d="M0 0 H720 V186 C580 128 440 128 330 152 L290 152 L180 72 L0 66 Z" fill="var(--navy)"/>
    <path d="M0 40 L230 52 L224 60 L0 54 Z" fill="var(--white)"/>
    <path d="M330 152 C440 128 580 128 720 186 L720 196 C580 140 440 140 330 158 Z" fill="var(--green)"/>
  </svg>

  <div class="brand">
    <div class="brand-row"><span class="brand-square"></span><span class="brand-name">Bayfield Capital Works, Inc</span></div>
    <div class="brand-tagline">Clear advice to buy or sell a neighborhood shop</div>
  </div>

  <ul class="contacts">
    <li><svg viewBox="0 0 14 14"><path d="M3 1 L5 1 L6 4 L4.5 5 C5.3 7 7 8.7 9 9.5 L10 8 L13 9 L13 11 C13 12 12 13 11 13 C5.5 13 1 8.5 1 3 C1 2 2 1 3 1 Z" fill="var(--green)"/></svg>(555) 806-2147</li>
    <li><svg viewBox="0 0 14 14"><rect x="3.5" y="1" width="7" height="12" rx="1.2" fill="none" stroke="var(--green)" stroke-width="1.4"/><circle cx="7" cy="11" r=".8" fill="var(--green)"/></svg>(555) 274-3918</li>
    <li><svg viewBox="0 0 14 14"><rect x="1" y="3" width="12" height="8.5" fill="none" stroke="var(--green)" stroke-width="1.4"/><path d="M1 3 L7 8 L13 3" fill="none" stroke="var(--green)" stroke-width="1.4"/></svg>g.harlow@bayfieldcapitalworks.example</li>
    <li><svg viewBox="0 0 14 14"><circle cx="7" cy="7" r="6" fill="none" stroke="var(--green)" stroke-width="1.4"/><path d="M1 7 H13 M7 1 C4 4 4 10 7 13 M7 1 C10 4 10 10 7 13" fill="none" stroke="var(--green)" stroke-width="1.1"/></svg>www.bayfieldcapitalworks.example</li>
  </ul>

  <div class="person">
    <div class="person-name">Glen R. Harlow</div>
    <div class="person-title">Small Business Advisor</div>
  </div>
  <div class="accent-tab"></div>
</section>

<section class="card card-back" aria-label="Card back">
  <div class="brand">
    <div class="brand-row"><span class="brand-square"></span><span class="brand-name">Bayfield Capital Works, Inc</span></div>
    <div class="brand-tagline">Clear advice to buy or sell a neighborhood shop</div>
  </div>
</section>

</body>
</html>
```